Flat Belly Design Graphics for Social

I want to create 9 social media graphics (new Instagram size 4:5 (1080 x 1350 pixels) focusing on our Flat Belly Graphics, using the pics attached. Use the attached pics, NO RANDOM STOCK PHOTOGRAPHY. For the color scheme of the graphics, the color palette is attached. YOU MUST POST ALL 9 GRAPHICS IN ONE ENTRY.
Using the 3 titles below, create one set of graphics. 1) with all text, then for the others, use the pictures as detailed below in IMPORTANT:
1. Ten-Week Bright Morning Reboot
2. The Quick Garden Kitchen Menu Guide
3. Studio Habits for Lasting Energy Past Midlife - Zero Gym Needed
IMPORTANT:
Only use RK Pic 1 and RK Pic 2 with the title, Ten-Week Bright Morning Reboot
Only use meal plan1 and meal plan2 pics with the title, Quick Garden Kitchen Menu Guide
Only use studio habits 1 and studio habits 2 pics with the title, Studio Habits for Lasting Energy Past Midlife - Zero Gym Needed
women over 40

```html
<!DOCTYPE html>
<html lang="en">
<head>
<meta charset="utf-8">
<title>Social Graphics Set</title>
<link href="https://fonts.googleapis.com/css2?family=Montserrat:wght@600;700;800&family=Oswald:wght@600;700&display=swap" rel="stylesheet">
<style>
:root{
  --board:#272727;
  --blush:#fbeced;
  --rose:#e39ab0;
  --rose-deep:#d2578a;
  --rose-soft:#f4b8cc;
  --pine:#1b5a4f;
  --slate:#2c4745;
  --sky:#5cc0d8;
  --white:#ffffff;
}
*{margin:0;padding:0;box-sizing:border-box}
html,body{width:960px;height:1200px;overflow:hidden;background:var(--board)}
.board{position:relative;width:960px;height:1200px}
.tile{position:absolute;width:231px;height:288px;background:var(--blush);overflow:hidden;font-family:"Montserrat",sans-serif;text-align:center;line-height:1}
.c1{left:110px}.c2{left:363px}.c3{left:616px}
.r1{top:132px}.r2{top:452px}.r3{top:772px}
.abs{position:absolute;left:0;right:0;line-height:1;white-space:nowrap}
.cond{font-family:"Oswald",sans-serif;font-weight:700;letter-spacing:-.5px}
.sans{font-family:"Montserrat",sans-serif;font-weight:800}
.photo{position:absolute}
.reboot-card{position:absolute;left:11px;top:9px;width:210px;height:270px;background:var(--blush);border-radius:8px}
.portrait-arch{background:linear-gradient(180deg,#e7a6b8,#d98ea4 60%,#c98a86)}
.food{background:radial-gradient(circle at 50% 50%,#6b4a33,#3e2a1e 70%)}
.friends{background:linear-gradient(120deg,#d9c6bd,#b88d78 50%,#f0e7e3)}
.vertical{position:absolute;text-align:center;white-space:normal}
</style>
</head>
<body>
<div class="board">

  <!-- Reboot: all text -->
  <section class="tile c1 r1">
    <svg class="abs" width="231" height="288" viewBox="0 0 231 288" style="top:0">
      <polygon points="0,0 123,0 100,9 0,9" fill="var(--rose)"/>
      <polygon points="0,0 10,0 10,112 0,118" fill="var(--rose)"/>
      <polygon points="231,170 222,176 222,278 231,288" fill="var(--rose)"/>
      <polygon points="115,288 130,279 231,279 231,288" fill="var(--rose)"/>
    </svg>
    <div class="reboot-card"></div>
    <div class="abs sans" style="top:50px;font-size:22px;color:var(--pine)">TEN-WEEK</div>
    <div class="abs sans" style="top:84px;font-size:36px;color:var(--slate)">BRIGHT</div>
    <div class="abs sans" style="top:128px;font-size:34px;color:var(--slate);letter-spacing:-1px">MORNING</div>
    <div class="abs sans" style="top:205px;font-size:24px;color:var(--rose-deep)">REBOOT</div>
  </section>

  <!-- Menu guide: all text -->
  <section class="tile c2 r1">
    <svg class="abs" width="231" height="120" viewBox="0 0 231 120" style="top:0">
      <polygon points="0,0 231,0 231,66 115,112 0,66" fill="var(--rose-soft)" opacity=".5"/>
      <polygon points="0,0 231,0 231,60 115,105 0,60" fill="var(--rose)"/>
    </svg>
    <div class="abs cond" style="top:28px;font-size:34px;color:var(--white)">THE QUICK</div>
    <div class="abs sans" style="top:116px;font-size:44px;color:var(--pine);letter-spacing:-1px">GARDEN</div>
    <div class="abs sans" style="top:180px;font-size:31px;color:var(--slate)">KITCHEN</div>
    <div class="abs sans" style="top:234px;font-size:24px;color:var(--pine)">MENU GUIDE</div>
  </section>

  <!-- Studio habits: all text -->
  <section class="tile c3 r1">
    <div style="position:absolute;left:11px;top:13px;width:209px;height:165px;background:var(--rose)"></div>
    <div class="abs cond" style="top:26px;font-size:30px;color:var(--blush)">STUDIO HABITS</div>
    <div class="abs cond" style="top:78px;font-size:30px;color:var(--blush)">FOR LASTING</div>
    <div class="abs cond" style="top:130px;font-size:30px;color:var(--blush)">ENERGY PAST</div>
    <div class="abs cond" style="top:188px;font-size:50px;color:var(--pine)">MIDLIFE</div>
    <div class="abs sans" style="top:256px;font-size:15px;font-weight:700;color:var(--rose-deep)">ZERO GYM NEEDED</div>
  </section>

  <!-- Reboot with portrait -->
  <section class="tile c1 r2">
    <div class="photo portrait-arch" role="img" aria-label="Smiling woman in a white cropped sweater pointing to her waist" style="left:0;top:0;width:231px;height:186px;border-radius:0 0 50% 50% / 0 0 18% 18%"></div>
    <svg class="abs" width="231" height="60" viewBox="0 0 231 60" style="top:140px">
      <path d="M0,30 Q100,68 231,0 L231,14 Q110,70 0,30 Z" fill="var(--pine)"/>
    </svg>
    <div class="abs sans" style="top:200px;font-size:21px;color:var(--pine)">TEN-WEEK</div>
    <div class="abs sans" style="top:226px;font-size:20px;color:var(--slate)">BRIGHT MORNING</div>
    <div class="abs sans" style="top:253px;font-size:20px;color:var(--rose-deep)">REBOOT</div>
  </section>

  <!-- Menu guide with food -->
  <section class="tile c2 r2">
    <div style="position:absolute;left:0;top:0;width:231px;height:72px;background:var(--rose)"></div>
    <div class="photo food" role="img" aria-label="Overhead view of chicken, fruit, vegetables and a written meal plan sheet" style="left:18px;top:14px;width:193px;height:128px;border:3px solid var(--blush)"></div>
    <div class="abs cond" style="top:150px;font-size:34px;color:var(--pine)">THE QUICK</div>
    <div class="abs sans" style="top:196px;font-size:19px;color:var(--slate)">GARDEN KITCHEN</div>
    <div style="position:absolute;left:0;top:230px;width:231px;height:40px;background:var(--rose)"></div>
    <div class="abs sans" style="top:238px;font-size:24px;color:var(--white)">MENU GUIDE</div>
  </section>

  <!-- Studio habits with friends -->
  <section class="tile c3 r2">
    <div class="abs cond" style="top:18px;font-size:26px;color:var(--slate)">STUDIO HABITS</div>
    <div class="abs sans" style="top:54px;font-size:15px;font-weight:700;color:var(--rose-deep)">FOR LASTING ENERGY</div>
    <div class="abs sans" style="top:74px;font-size:23px;color:var(--pine);letter-spacing:-.5px">PAST MIDLIFE</div>
    <div style="position:absolute;left:0;top:106px;width:231px;height:28px;background:var(--rose)"></div>
    <div class="abs sans" style="top:113px;font-size:14px;font-weight:700;color:var(--white)">ZERO GYM NEEDED</div>
    <div class="photo friends" role="img" aria-label="Two women sharing a whispered secret, one looking surprised" style="left:0;top:134px;width:231px;height:154px"></div>
  </section>

  <!-- Reboot with vertical title -->
  <section class="tile c1 r3">
    <div class="photo portrait-arch" role="img" aria-label="Smiling woman in a white cropped sweater and black jeans" style="left:80px;top:0;width:151px;height:288px"></div>
    <div style="position:absolute;left:5px;top:7px;width:114px;height:275px;background:var(--rose-soft);opacity:.92"></div>
    <div class="vertical sans" style="left:12px;top:22px;width:34px;font-size:27px;line-height:36px;color:var(--white)">T<br>E<br>N</div>
    <div class="vertical sans" style="left:54px;top:14px;width:46px;font-size:36px;line-height:40px;color:var(--pine)">W<br>E<br>E<br>K</div>
    <div class="abs sans" style="top:186px;left:5px;width:114px;font-size:22px;color:var(--pine);text-align:left;padding-left:6px">BRIGHT</div>
    <div class="abs sans" style="top:220px;left:5px;width:114px;font-size:14px;font-weight:700;color:var(--white);text-align:left;padding-left:7px;line-height:24px;white-space:normal">MORNING<br>REBOOT</div>
  </section>

  <!-- Menu guide over food -->
  <section class="tile c2 r3">
    <div class="photo food" role="img" aria-label="Fresh produce, salmon and eggs framing a small meal plan notebook on a dark table" style="left:0;top:136px;width:231px;height:152px"></div>
    <div style="position:absolute;left:15px;top:14px;width:201px;height:152px;background:var(--rose);border:3px solid var(--blush)"></div>
    <div class="abs cond" style="top:34px;font-size:32px;color:var(--white)">THE QUICK</div>
    <div class="abs sans" style="top:82px;font-size:18px;color:var(--blush)">GARDEN KITCHEN</div>
    <div class="abs sans" style="top:114px;font-size:24px;color:var(--pine)">MENU GUIDE</div>
  </section>

  <!-- Studio habits on sky -->
  <section class="tile c3 r3" style="background:var(--sky)">
    <div class="photo friends" role="img" aria-label="Two women against a blue backdrop, one whispering to the other" style="left:75px;top:8px;width:156px;height:240px;opacity:.85"></div>
    <div class="vertical sans" style="left:12px;top:50px;font-size:13px;line-height:23px;color:var(--white);text-align:left">STUDIO<br>HABITS<br>FOR</div>
    <div class="vertical sans" style="left:12px;top:120px;font-size:20px;line-height:30px;color:var(--white);text-align:left">LASTING<br>ENERGY</div>
    <div class="abs cond" style="left:12px;right:auto;top:198px;font-size:36px;color:var(--white);text-align:left">PAST MIDLIFE</div>
    <div style="position:absolute;left:0;top:253px;width:231px;height:20px;background:var(--blush)"></div>
    <div class="abs sans" style="top:257px;font-size:13px;font-weight:700;color:var(--pine)">ZERO GYM NEEDED</div>
  </section>

</div>
</body>
</html>
```